Fernhale Business Card Design

We are looking for a fresh business card design for our new logo. We would like a business card that is unique but friendly. We are in the window coverings business offering blinds, shutters and shades for homes.

Target Market(s)

Targeting the end-consumer

Industry/Entity Type

Business

Requirements
Must have
• Must have a dedicates space for a photo of our sales person. Must contain our new logo (attached).

```html
<!DOCTYPE html>
<html lang="en">
<head>
<meta charset="utf-8">
<title>Fernhale Business Card</title>
<link href="https://fonts.googleapis.com/css2?family=Alegreya:wght@500&family=Work+Sans:wght@400;500&display=swap" rel="stylesheet">
<style>
  :root {
    --stage: #1b1b1b;
    --card-white: #ffffff;
    --card-black: #1e1e1e;
    --ink: #5d5e60;
    --ink-strong: #58595b;
    --leaf: #7dc242;
    --band-grey: #5f6062;
    --on-dark: #f4f4f4;
  }
  * { box-sizing: border-box; margin: 0; padding: 0; }
  html, body { width: 1200px; height: 897px; overflow: hidden; background: var(--stage); }
  .canvas { position: relative; width: 1200px; height: 897px; }
  .card {
    position: absolute; left: 304px; width: 594px; height: 338px;
    border-radius: 18px; overflow: hidden;
    font-family: "Work Sans", sans-serif;
  }
  .card-front { top: 92px; background: var(--card-white); }
  .card-back {
    top: 470px;
    background: radial-gradient(ellipse at 75% 60%, #333 0%, var(--card-black) 60%, #181818 100%);
  }
  .photo {
    position: absolute; left: 32px; top: 3px; width: 262px; height: 335px;
    background: linear-gradient(180deg, #e9e6e4 0%, #d7d2ce 45%, #4a4a4c 70%, #3a3a3c 100%);
    border-radius: 120px 120px 0 0;
  }
  .brand { position: absolute; display: flex; align-items: center; }
  .brand-mark { display: block; border-style: solid; border-radius: 4px; }
  .brand-name { font-family: "Alegreya", serif; font-weight: 500; line-height: 1; }
  .card-front .brand { left: 277px; top: 32px; }
  .card-front .brand-mark { width: 62px; height: 62px; border-width: 3px; border-color: var(--ink); }
  .card-front .brand-name { margin-left: 16px; font-size: 51px; color: var(--ink-strong); }
  .address {
    position: absolute; right: 28px; top: 139px; text-align: right;
    font-size: 13.5px; line-height: 17px; color: var(--ink);
  }
  .contacts { position: absolute; right: 28px; top: 192px; list-style: none; }
  .contacts li {
    display: flex; justify-content: flex-end; align-items: center;
    height: 19.3px; font-size: 14px; color: var(--ink); letter-spacing: 0.2px;
  }
  .contacts svg { width: 12px; height: 12px; margin-left: 12px; fill: var(--leaf); }
  .band-name {
    position: absolute; left: 0; top: 294px; width: 306px; height: 25px;
    background: var(--leaf); clip-path: polygon(0 0, 100% 0, 97% 100%, 0 100%);
    color: #fff; padding-left: 32px; display: flex; align-items: center;
  }
  .person-name { font-size: 17px; font-weight: 500; letter-spacing: 1px; }
  .person-role { font-size: 13.5px; margin-left: 9px; letter-spacing: 0.5px; }
  .band-social {
    position: absolute; left: 298px; top: 294px; width: 296px; height: 25px;
    background: var(--band-grey); clip-path: polygon(3% 0, 100% 0, 100% 100%, 0 100%);
    color: #fff; font-size: 13.5px; letter-spacing: 0.5px;
    display: flex; align-items: center; justify-content: flex-end; padding-right: 30px;
  }
  .card-back .brand { left: 96px; top: 124px; }
  .card-back .brand-mark { width: 88px; height: 88px; border-width: 3px; border-color: var(--on-dark); }
  .card-back .brand-name { margin-left: 22px; font-size: 66px; color: var(--on-dark); }
  .back-url {
    position: absolute; left: 0; right: 0; top: 299px; text-align: center;
    font-size: 13px; letter-spacing: 1px; color: var(--on-dark);
  }
</style>
</head>
<body>
<div class="canvas">
  <section class="card card-front">
    <div class="photo" role="img" aria-label="Portrait photo of the sales person"></div>
    <div class="brand">
      <span class="brand-mark"></span>
      <span class="brand-name">Fernhale</span>
    </div>
    <p class="address">P.O.Box: 214,<br>Riverton Bay, Avalon</p>
    <ul class="contacts">
      <li>(021) 555-0148<svg viewBox="0 0 24 24"><path d="M6.6 10.8a15 15 0 0 0 6.6 6.6l2.2-2.2c.3-.3.7-.4 1-.2 1.1.4 2.3.6 3.6.6.6 0 1 .4 1 1V20c0 .6-.4 1-1 1A17 17 0 0 1 3 4c0-.6.4-1 1-1h3.5c.6 0 1 .4 1 1 0 1.3.2 2.5.6 3.6.1.3 0 .7-.2 1z"/></svg></li>
      <li>(021) 555-0148<svg viewBox="0 0 24 24"><path d="M7 1h10a2 2 0 0 1 2 2v18a2 2 0 0 1-2 2H7a2 2 0 0 1-2-2V3a2 2 0 0 1 2-2zm0 3v14h10V4zm5 15.5a1 1 0 1 0 0 2 1 1 0 0 0 0-2z"/></svg></li>
      <li>(021) 555-0149<svg viewBox="0 0 24 24"><path d="M6 2h12v5H6zM3 8h18a2 2 0 0 1 2 2v7h-4v5H5v-5H1v-7a2 2 0 0 1 2-2zm4 8v4h10v-4z"/></svg></li>
      <li>info@lumenhome.com<svg viewBox="0 0 24 24"><path d="M2 5h20v14H2zm2 2v.5l8 5 8-5V7l-8 5z"/></svg></li>
      <li>www.lumenhome.com<svg viewBox="0 0 24 24"><path d="M12 2a10 10 0 1 0 0 20 10 10 0 0 0 0-20zm0 2c.9 1.2 1.6 2.6 2 4h-4c.4-1.4 1.1-2.8 2-4zM4.3 14a8 8 0 0 1 0-4h3.4a16 16 0 0 0 0 4zm5.4 0a14 14 0 0 1 0-4h4.6a14 14 0 0 1 0 4zm6.6 0a16 16 0 0 0 0-4h3.4a8 8 0 0 1 0 4zM10 16h4c-.4 1.4-1.1 2.8-2 4-.9-1.2-1.6-2.6-2-4z"/></svg></li>
    </ul>
    <div class="band-name"><span class="person-name">DANA WHITLOCK</span><span class="person-role">REALTOR</span></div>
    <div class="band-social">@fernhalehome</div>
  </section>

  <section class="card card-back">
    <div class="brand">
      <span class="brand-mark"></span>
      <span class="brand-name">Fernhale</span>
    </div>
    <p class="back-url">www.fernhaleshades.com</p>
  </section>
</div>
</body>
</html>
```